Business card for Eyelash extension salon in Beverly Hills,California USA

We need new business card for our salon in Beverly Hills. The salon name is 'Lashvera' . We would like to have...Business name: Lashvera Name of person: will provide later Address 4720 N.Alder Crest Ave Beverly Hills , CA 90210 Phone: will provide later (Text only) Web: www.lashverastudio.example Snapgrid icon, Circlebook icon follow us for seasonal campaign and news @lashverastudiolounge Design should look elegant, high-end, clean, simple, cohesive with my brand. Please refer my brand board. Business name color will be metallic bronzy color. Im thinking grey background or white background. Thanks

Target Market(s)

25-35. Gender neutral. People who are in Entertainment business industry.
This is High-end Eyelash extension salon in Beverly Hills

Industry/Entity Type

Beauty Salon

Contact Information for Business Card

Business name: Lashvera
Name of person: will provide later
Address 4720 N.Alder Crest Ave Beverly Hills , CA 90210
Phone: will provide later (Text only)
Web: www.lashverastudio.example
Snapgrid icon, Circlebook icon
follow us for seasonal campaign and news @lashverastudiolounge

Requirements
Must have
• Beautiful, elegant, clean and simple look but very attractive and modern
Should not have
• We don't like too clutter, too busy designs.

```html
<!DOCTYPE html>
<html lang="en">
<head>
<meta charset="utf-8">
<title>Lashvera – Business Card</title>
<link rel="stylesheet" href="https://fonts.googleapis.com/css2?family=Playfair+Display:wght@700&family=Work+Sans:wght@300;400;500&display=swap">
<style>
  :root {
    --stage: #262626;
    --bronze: #8b6a52;
    --bronze-ink: #7a5a44;
    --paper: #f4f4f4;
    --ink: #1c1c1c;
    --white: #ffffff;
    --rule: #a88a74;
  }
  * { box-sizing: border-box; margin: 0; padding: 0; }
  html, body {
    width: 1200px; height: 800px; overflow: hidden;
    background: var(--stage);
    font-family: "Work Sans", sans-serif;
  }
  .stage {
    position: relative; width: 1200px; height: 800px;
    display: flex; flex-direction: column; align-items: center; justify-content: center; gap: 36px;
  }
  .card {
    position: relative; width: 620px; height: 354px;
    box-shadow: 0 10px 30px rgba(0,0,0,.45);
    overflow: hidden;
  }
  .card--front { background: var(--bronze); color: var(--white); }
  .card--back { background: var(--paper); color: var(--ink); }

  .brand-name {
    position: absolute; right: 60px; top: 168px;
    font-weight: 300; font-size: 58px; line-height: 1; letter-spacing: 1px; color: var(--white);
    white-space: nowrap;
  }
  .social {
    position: absolute; left: 58px; top: 226px;
    display: flex; align-items: center; gap: 16px;
    font-size: 13px; letter-spacing: .6px; white-space: nowrap;
  }
  .social__item { display: flex; align-items: center; gap: 6px; }
  .social__dot { width: 9px; height: 9px; background: var(--white); border-radius: 50%; }

  .person {
    position: absolute; left: 58px; top: 112px;
  }
  .person__name {
    font-family: "Playfair Display", serif; font-weight: 700;
    font-size: 25px; color: var(--bronze-ink); letter-spacing: .5px; white-space: nowrap;
  }
  .person__title {
    margin-top: 4px; font-size: 12px; letter-spacing: 3.4px; color: var(--ink); white-space: nowrap;
  }
  .divider {
    position: absolute; left: 58px; right: 50px; top: 200px;
    height: 1px; background: var(--rule);
  }
  .contact {
    position: absolute; left: 50px; right: 20px; top: 228px;
    font-size: 13px; letter-spacing: .8px; line-height: 30px;
  }
  .contact__row { display: flex; gap: 18px; white-space: nowrap; }
  .contact__label { color: var(--bronze-ink); margin-right: 8px; font-weight: 500; }
</style>
</head>
<body>
  <main class="stage">
    <section class="card card--front" aria-label="Card front">
      <div class="social">
        <span class="social__item"><span class="social__dot"></span>Snapgrid</span>
        <span class="social__item"><span class="social__dot"></span>Circlebook</span>
        <span class="social__handle">@lashverastudiolounge</span>
      </div>
      <div class="brand-name">Lashvera</div>
    </section>

    <section class="card card--back" aria-label="Card back">
      <div class="person">
        <div class="person__name">MIRELO DASANTE</div>
        <div class="person__title">Creative &amp; Director</div>
      </div>
      <div class="divider"></div>
      <div class="contact">
        <div class="contact__row">
          <span><span class="contact__label">A</span>4720 N.Alder Crest Ave Beverly Hills , CA 90210</span>
        </div>
        <div class="contact__row">
          <span><span class="contact__label">E</span>hi@lashvera.example</span>
          <span><span class="contact__label">W</span>lashverastudio.example</span>
          <span><span class="contact__label">T</span>555-014-0276</span>
        </div>
      </div>
    </section>
  </main>
</body>
</html>
```